Home Remodeling company needs a business card design

we need a business card design for home remodeling company in hamilton county, indiana USA. we offers a wide range of construction services including whole house renovations, Design and Build Basements and Kitchen and Bathroom Remodeling . we would like to see designs for both site of business card that use the same color of the company logo and also including all information below :
1- Karim Feltous CEO / General Contractor
2- all company contacts Telephone numbers ( 1-888-DULOM-47 ) ( 317-555-0193) email address ( info@dulomhome.com) website ( www.dulomhome.com ) and social media logos (Facebook- twitter- google plus )
3- company logo
4- licensed . insured . bonded

```html
<!DOCTYPE html>
<html lang="en">
<head>
<meta charset="UTF-8">
<title>DULOM Home Remodeling – Business Card</title>
<link href="https://fonts.googleapis.com/css2?family=Roboto:wght@400;500;700;900&display=swap" rel="stylesheet">
<style>
  :root {
    --backdrop: #e6e3df;
    --card-dark: #333333;
    --card-light: #f1f1f1;
    --accent-red: #d3232c;
    --text-light: #ffffff;
    --text-muted: #d8d8d8;
    --logo-dark: #2a2a2a;
    --logo-grey: #8a8a8a;
  }
  * { margin: 0; padding: 0; box-sizing: border-box; }
  html, body { width: 1200px; height: 716px; overflow: hidden; }
  body {
    background: var(--backdrop);
    font-family: "Roboto", Arial, sans-serif;
    position: relative;
  }
  .card {
    position: absolute;
    width: 520px;
    height: 300px;
    top: 208px;
    border-radius: 3px;
    overflow: hidden;
    box-shadow: 0 10px 24px rgba(0,0,0,0.22);
  }
  /* Front */
  .card-front { left: 50px; background: var(--card-dark); }
  .front-logo {
    position: absolute;
    left: 0; right: 0; top: 98px;
    text-align: center;
    color: var(--text-light);
  }
  .brand-name {
    display: inline-flex; align-items: center; gap: 10px;
    font-weight: 900; font-size: 58px; letter-spacing: 3px; line-height: 1;
  }
  .brand-mark { width: 12px; height: 12px; background: currentColor; display: inline-block; }
  .brand-tagline {
    margin-top: 8px;
    font-weight: 500; font-size: 15px; letter-spacing: 7px;
  }
  /* Back */
  .card-back { left: 630px; background: var(--card-dark); }
  .back-shape { position: absolute; inset: 0; }
  .back-logo {
    position: absolute;
    left: 108px; top: 150px;
    transform: translate(-50%, -50%) rotate(-90deg);
    white-space: nowrap;
    text-align: center;
  }
  .back-logo .brand-name { font-size: 46px; color: var(--logo-dark); }
  .back-logo .brand-mark { background: var(--accent-red); width: 10px; height: 10px; }
  .back-logo .brand-tagline { color: var(--logo-grey); font-size: 12px; letter-spacing: 5px; margin-top: 4px; }
  .contact-block {
    position: absolute;
    left: 285px; top: 44px;
    color: var(--text-light);
  }
  .person-name { font-weight: 700; font-size: 20px; letter-spacing: 0.5px; }
  .person-title { font-size: 12px; color: var(--text-muted); margin-top: 2px; }
  .contact-list { list-style: none; margin-top: 16px; }
  .contact-list li {
    display: flex; align-items: center; gap: 10px;
    font-size: 14px; line-height: 21px;
  }
  .contact-list svg { width: 11px; height: 11px; fill: var(--text-light); flex: none; }
  .social-row {
    display: flex; align-items: center; gap: 5px;
    margin-top: 12px; font-size: 14px;
  }
  .social-row .label { margin-right: 5px; }
  .social-square { width: 17px; height: 17px; background: var(--text-light); border-radius: 2px; }
  .credentials { margin-top: 8px; font-size: 15px; letter-spacing: 0.3px; }
</style>
</head>
<body>
  <section class="card card-front" aria-label="Card front">
    <div class="front-logo">
      <div class="brand-name">DULOM<span class="brand-mark"></span></div>
      <div class="brand-tagline">HOME REMODELING</div>
    </div>
  </section>

  <section class="card card-back" aria-label="Card back">
    <svg class="back-shape" viewBox="0 0 520 300" preserveAspectRatio="none">
      <path d="M0 0 H232 C272 90 244 222 150 300 H0 Z" fill="var(--card-light)"/>
      <path d="M246 -2 C288 92 258 226 166 302" fill="none" stroke="var(--accent-red)" stroke-width="5"/>
    </svg>

    <div class="back-logo">
      <div class="brand-name">DULOM<span class="brand-mark"></span></div>
      <div class="brand-tagline">HOME REMODELING</div>
    </div>

    <div class="contact-block">
      <div class="person-name">Karim Feltous</div>
      <div class="person-title">CEO / General Contractor</div>
      <ul class="contact-list">
        <li><svg viewBox="0 0 12 12"><path d="M2.5 1 L4.5 1 L5 3.5 L3.8 4.4 C4.4 5.8 6.2 7.6 7.6 8.2 L8.5 7 L11 7.5 L11 9.5 C11 10.3 10.3 11 9.5 11 C5 11 1 7 1 2.5 C1 1.7 1.7 1 2.5 1Z"/></svg>1-888-DULOM-47</li>
        <li><svg viewBox="0 0 12 12"><rect x="1" y="4" width="10" height="7" rx="1"/><rect x="3" y="1" width="6" height="4" fill="none" stroke="#fff" stroke-width="1"/></svg>317-555-0193</li>
        <li><svg viewBox="0 0 12 12"><path d="M1 2.5 H11 V9.5 H1 Z M1.5 3 L6 6.5 L10.5 3" fill="none" stroke="#fff" stroke-width="1.3"/></svg>info@dulomhome.com</li>
        <li><svg viewBox="0 0 12 12"><circle cx="6" cy="6" r="5" fill="none" stroke="#fff" stroke-width="1.2"/><path d="M1 6 H11 M6 1 C3.5 3.5 3.5 8.5 6 11 M6 1 C8.5 3.5 8.5 8.5 6 11" fill="none" stroke="#fff" stroke-width="1"/></svg>www.dulomhome.com</li>
      </ul>
      <div class="social-row">
        <span class="label">Follows on:</span>
        <span class="social-square"></span>
        <span class="social-square"></span>
        <span class="social-square"></span>
      </div>
      <div class="credentials">Licensed&nbsp;&nbsp;•&nbsp;&nbsp;Insured&nbsp;&nbsp;•&nbsp;&nbsp;Bonded</div>
    </div>
  </section>
</body>
</html>
```